holloway paving service

Needs to have phone number 0418259730 and email markholloway@brightmail.com.au.
ABN 62318470915
name mark holloway

For all your concreting solutions
Excavation
Exposed & colour concrete
House & shed slabs
Driveways
Landing & steps

Contact Information for Business Card

ph 0418259730
email markholloway@brightmail.com.au.
ABN 62318470915
name mark holloway

```html
<!DOCTYPE html>
<html lang="en">
<head>
<meta charset="utf-8">
<title>Holloway Paving Service – Business Card</title>
<link rel="stylesheet" href="https://fonts.googleapis.com/css2?family=Lato:wght@400;700&family=Montserrat:wght@500;600&display=swap">
<style>
  :root {
    --orange: #e8652a;
    --orange-dark: #c9521c;
    --orange-light: #f07232;
    --ink: #4a4a4a;
    --grey: #6b6b6b;
    --white: #ffffff;
    --paper: #f6f6f6;
    --stage: #1c1c1c;
  }
  * { box-sizing: border-box; margin: 0; padding: 0; }
  html, body { width: 1200px; height: 963px; overflow: hidden; }
  body {
    background: var(--stage);
    font-family: "Lato", Arial, sans-serif;
    display: flex;
    flex-direction: column;
    align-items: center;
    justify-content: center;
    gap: 56px;
  }
  .card {
    position: relative;
    width: 660px;
    height: 377px;
    border-radius: 2px;
    overflow: hidden;
    box-shadow: 0 10px 30px rgba(0,0,0,.5);
  }

  /* Front */
  .card-front { background: linear-gradient(135deg, var(--white) 40%, var(--paper)); }
  .holder {
    position: absolute; left: 0; top: 36px;
    display: flex; gap: 14px; align-items: flex-start;
  }
  .holder-tab { width: 28px; height: 30px; background: var(--orange); }
  .holder-name {
    font-family: "Montserrat", Arial, sans-serif;
    font-weight: 500; font-size: 26px; letter-spacing: 1px;
    color: var(--orange); text-transform: uppercase; line-height: 1;
  }
  .holder-role { font-size: 14px; color: var(--grey); margin-top: 4px; }

  .brand {
    position: absolute; display: flex; align-items: center; gap: 14px;
  }
  .card-front .brand { right: 40px; top: 160px; }
  .brand-square { width: 44px; height: 44px; background: var(--orange); }
  .brand-rule { width: 1px; height: 62px; background: var(--orange); }
  .brand-name {
    font-family: "Lato", Arial, sans-serif; font-weight: 700;
    font-size: 15px; letter-spacing: 1px; text-transform: uppercase;
    color: var(--orange); line-height: 1.25;
  }
  .brand-phone { font-size: 12px; letter-spacing: 2px; color: var(--ink); margin-top: 2px; }

  .contacts {
    position: absolute; left: 40px; bottom: 60px;
    list-style: none; font-size: 15px; color: var(--ink); line-height: 1.5;
  }
  .contacts li { display: flex; align-items: center; gap: 10px; }
  .contacts svg { width: 12px; height: 12px; fill: none; stroke: var(--orange); stroke-width: 2; }
  .accent { color: var(--orange); }

  .address {
    position: absolute; right: 40px; bottom: 34px; text-align: right;
    font-size: 16px; color: var(--ink); line-height: 1.35;
  }
  .address .locality { color: var(--orange); }

  /* Back */
  .card-back { background: linear-gradient(135deg, var(--orange-dark), var(--orange-light) 55%, var(--orange-dark)); }
  .card-back .brand { left: 70px; top: 110px; gap: 22px; }
  .card-back .brand-square { width: 96px; height: 96px; background: #efefef; }
  .card-back .brand-rule { height: 120px; background: rgba(255,255,255,.8); }
  .card-back .brand-name { color: var(--white); font-size: 24px; }
  .card-back .brand-phone { color: var(--white); font-size: 18px; letter-spacing: 3px; }
  .website {
    position: absolute; left: 70px; bottom: 50px;
    color: var(--white); font-size: 17px; letter-spacing: .5px;
  }
</style>
</head>
<body>

  <section class="card card-front" aria-label="Business card front">
    <div class="holder">
      <div class="holder-tab"></div>
      <div>
        <div class="holder-name">Mark Holloway</div>
        <div class="holder-role">Director</div>
      </div>
    </div>

    <div class="brand">
      <div class="brand-square"></div>
      <div class="brand-rule"></div>
      <div>
        <div class="brand-name">Holloway Paving<br>Service</div>
        <div class="brand-phone">0418259730</div>
      </div>
    </div>

    <ul class="contacts">
      <li><svg viewBox="0 0 12 12"><path d="M3 1l2 3-1.5 1.5a6 6 0 0 0 3 3L8 7l3 2-1.5 2A9 9 0 0 1 1 2.5z"/></svg>+61 418 259 730</li>
      <li><svg viewBox="0 0 12 12"><rect x="1" y="2.5" width="10" height="7"/><path d="M1 2.5l5 4 5-4"/></svg>markholloway@brightmail.com.au</li>
      <li><svg viewBox="0 0 12 12"><circle cx="6" cy="6" r="5"/><path d="M1 6h10M6 1c2 2.5 2 7.5 0 10M6 1c-2 2.5-2 7.5 0 10"/></svg><span>www.<span class="accent">hollowaypaving</span>.com.au</span></li>
    </ul>

    <div class="address">
      <div class="locality">Eastvale</div>
      <div>Harbourton, Tasmania 7390</div>
    </div>
  </section>

  <section class="card card-back" aria-label="Business card back">
    <div class="brand">
      <div class="brand-square"></div>
      <div class="brand-rule"></div>
      <div>
        <div class="brand-name">Holloway Paving<br>Service</div>
        <div class="brand-phone">0418259730</div>
      </div>
    </div>
    <div class="website">www.hollowaypaving.com.au</div>
  </section>

</body>
</html>
```